Accounting firm needing business card / letterhead designed
Marcus L. Trenholm, CPA
marcus@veltrowledger.com
www.veltrowledger.com
842 E Alder Ave Calder Falls, WI 43827
555-562-0974

```html
<!DOCTYPE html>
<html lang="en">
<head>
<meta charset="utf-8">
<title>Veltrow Ledger — Business Card</title>
<link rel="stylesheet" href="https://fonts.googleapis.com/css2?family=Michroma&family=Roboto:wght@400;500&family=Roboto+Condensed:wght@500&display=swap">
<style>
  :root {
    --navy: #272264;
    --green: #8dc63f;
    --paper: #f7f7f7;
    --backdrop: #c9c9c9;
    --ink-grey: #555555;
    --white: #ffffff;
  }
  * { margin: 0; padding: 0; box-sizing: border-box; }
  html, body { width: 1200px; height: 960px; overflow: hidden; }
  body {
    background: var(--backdrop);
    position: relative;
    font-family: "Roboto", Arial, sans-serif;
  }
  .card {
    position: absolute;
    width: 600px;
    height: 344px;
    border-radius: 18px;
    background: var(--paper);
    overflow: hidden;
  }
  .card--front { left: 320px; top: 100px; }
  .card--back  { left: 320px; top: 493px; }

  .wordmark {
    font-family: "Michroma", Arial, sans-serif;
    font-weight: 400;
    color: var(--navy);
    white-space: nowrap;
    position: absolute;
  }
  .card--front .wordmark {
    left: 0; right: 0; top: 150px;
    text-align: center;
    font-size: 30px;
    letter-spacing: 1px;
  }
  .card--front .website {
    position: absolute;
    left: 0; right: 0; top: 290px;
    text-align: center;
    font-size: 15px;
    letter-spacing: 6.5px;
    color: var(--ink-grey);
  }

  .back-art { position: absolute; inset: 0; }
  .card--back .wordmark {
    right: 30px; top: 62px;
    font-size: 19px;
  }
  .contact {
    position: absolute;
    left: 34px; top: 174px;
    color: var(--white);
  }
  .contact__name {
    font-family: "Roboto Condensed", "Roboto", Arial, sans-serif;
    font-size: 21px;
    font-weight: 500;
    line-height: 26px;
    margin-bottom: 8px;
  }
  .contact__address { font-size: 14px; line-height: 18px; margin-bottom: 11px; }
  .contact__list { list-style: none; font-size: 14px; line-height: 19px; }
  .contact__list li { display: flex; align-items: center; gap: 9px; }
  .contact__list svg { width: 14px; height: 14px; flex: none; }
  .icon-solid { fill: var(--white); }
  .icon-globe { fill: none; stroke: var(--white); stroke-width: 2.2; }
</style>
</head>
<body>

<section class="card card--front">
  <div class="wordmark">VELTROW LEDGER</div>
  <div class="website">www.veltrowledger.com</div>
</section>

<section class="card card--back">
  <svg class="back-art" viewBox="0 0 600 344" width="600" height="344" aria-hidden="true">
    <path d="M280 0 C296 130 368 262 492 344 C360 262 276 128 243 0 Z" fill="var(--green)"/>
    <path d="M0 0 H239 C271 128 350 262 490 344 H0 Z" fill="var(--navy)"/>
    <path d="M239 0 C271 128 350 262 490 344" fill="none" stroke="var(--white)" stroke-width="3"/>
  </svg>

  <div class="wordmark">VELTROW LEDGER</div>

  <div class="contact">
    <div class="contact__name">Marcus L. Trenholm, CPA</div>
    <div class="contact__address">842 E Alder Ave<br>Calder Falls, WI 43827</div>
    <ul class="contact__list">
      <li>
        <svg class="icon-solid" viewBox="0 0 24 24"><path d="M6.6 10.8a15.1 15.1 0 0 0 6.6 6.6l2.2-2.2c.3-.3.7-.4 1-.2 1.1.4 2.3.6 3.6.6.6 0 1 .4 1 1V20c0 .6-.4 1-1 1A17 17 0 0 1 3 4c0-.6.4-1 1-1h3.5c.6 0 1 .4 1 1 0 1.3.2 2.5.6 3.6.1.3 0 .7-.2 1z"/></svg>
        555-562-0974
      </li>
      <li>
        <svg class="icon-solid" viewBox="0 0 24 24"><path d="M2 5h20v2l-10 6L2 7z M2 9l10 6 10-6v10H2z"/></svg>
        marcus@veltrowledger.com
      </li>
      <li>
        <svg class="icon-globe" viewBox="0 0 24 24"><circle cx="12" cy="12" r="9.5"/><path d="M2.5 12h19M12 2.5c3 3 3 16 0 19M12 2.5c-3 3-3 16 0 19"/></svg>
        www.veltrowledger.com
      </li>
    </ul>
  </div>
</section>

</body>
</html>
```